New Business Card Design Project

Need a design that will create an impact / strong impression towards our clients for our business. We are in the lighting business and we do lighting retrofits for large commercial to industrial clientele.

Target Market(s)

Lighting Industry

Industry/Entity Type

Business

Font styles to use
Other font styles liked:
• we would like to use the font on our logo, not sure what it is though..

Requirements
Must have
• Our logo.
Nice to have
• We are open to suggestions that have to do with lighting.

```html
<!DOCTYPE html>
<html lang="en">
<head>
<meta charset="utf-8">
<title>Corvane Retrofit Group — Business Card</title>
<link rel="stylesheet" href="https://fonts.googleapis.com/css2?family=Montserrat:wght@400;500;700&display=swap">
<style>
  :root {
    --backdrop: #2b2b2b;
    --green: #0b8437;
    --green-deep: #143d15;
    --green-light: #67c75a;
    --card-white: #ffffff;
    --card-back: #efefef;
    --ink-grey: #4a4a4a;
  }
  * { margin: 0; padding: 0; box-sizing: border-box; }
  html, body { width: 1200px; height: 960px; overflow: hidden; }
  body {
    background: var(--backdrop);
    font-family: "Montserrat", sans-serif;
    position: relative;
  }
  .card {
    position: absolute;
    width: 600px;
    height: 343px;
    overflow: hidden;
  }
  .card-front { left: 314px; top: 113px; background: var(--card-white); }
  .card-back { left: 311px; top: 472px; background: var(--card-back); }

  .front-shape { position: absolute; inset: 0; }
  .edge-band {
    position: absolute; right: 0; top: 0;
    width: 20px; height: 100%;
    background: var(--green-deep);
  }

  .brand-front {
    position: absolute;
    left: 272px; top: 36px;
    width: 254px;
    display: flex; align-items: center; gap: 10px;
  }
  .brand-square {
    width: 34px; height: 34px; flex: none;
    background: var(--green);
  }
  .brand-name {
    color: var(--green-deep);
    font-weight: 700;
    line-height: 1.1;
  }
  .brand-front .brand-name { font-size: 15px; letter-spacing: 0.5px; }

  .contact {
    position: absolute;
    left: 27px; top: 110px;
    color: #ffffff;
  }
  .person-name { font-size: 19px; font-weight: 700; line-height: 24px; }
  .person-title { font-size: 15px; font-weight: 400; line-height: 20px; }
  .address { margin-top: 12px; font-size: 15px; line-height: 19.5px; }
  .lines { margin-top: 6px; list-style: none; }
  .lines li {
    display: flex; align-items: center; gap: 8px;
    font-size: 15px; line-height: 19px;
  }
  .lines svg { width: 14px; height: 14px; flex: none; fill: #ffffff; }

  .brand-back {
    position: absolute;
    left: 0; right: 0; top: 130px;
    display: flex; justify-content: center; align-items: center; gap: 16px;
  }
  .brand-back .brand-square { width: 56px; height: 56px; }
  .brand-back .brand-name { font-size: 40px; letter-spacing: 2px; }
  .back-url {
    position: absolute;
    left: 0; right: 0; top: 281px;
    text-align: center;
    font-size: 14px;
    letter-spacing: 2.4px;
    color: var(--ink-grey);
  }
</style>
</head>
<body>
  <section class="card card-front">
    <svg class="front-shape" viewBox="0 0 600 343" aria-hidden="true">
      <polygon points="0,0 137,0 377,343 0,343" fill="var(--green)"/>
    </svg>
    <div class="edge-band"></div>

    <div class="brand-front">
      <span class="brand-square"></span>
      <span class="brand-name">CORVANE RETROFIT GROUP, LLC</span>
    </div>

    <div class="contact">
      <p class="person-name">DANIEL REYES</p>
      <p class="person-title">CEO/FOUNDER</p>
      <p class="address">214 Alder Court<br>Kodiak<br>Alaska 99615</p>
      <ul class="lines">
        <li><svg viewBox="0 0 14 14"><path d="M1 5c0-2 2-3 6-3s6 1 6 3v1h-3V5H4v1H1z M3 7h8l1 5H2z"/></svg>555 204 7781</li>
        <li><svg viewBox="0 0 14 14"><path d="M4 0h6a1 1 0 0 1 1 1v12a1 1 0 0 1-1 1H4a1 1 0 0 1-1-1V1a1 1 0 0 1 1-1zm1 2v9h4V2z"/></svg>555 318 6402</li>
        <li><svg viewBox="0 0 14 14"><path d="M4 1h6v4H4z M1 6h12v5h-2V9H3v2H1z M3 10h8v3H3z"/></svg>555 762 0915</li>
        <li><svg viewBox="0 0 14 14"><path d="M1 3h12v1L7 8 1 4z M1 5.5l6 4 6-4V11H1z"/></svg>hello@corvane.example</li>
        <li><svg viewBox="0 0 14 14"><circle cx="7" cy="7" r="6"/></svg>www.corvane.example</li>
      </ul>
    </div>
  </section>

  <section class="card card-back">
    <div class="brand-back">
      <span class="brand-square"></span>
      <span class="brand-name">CORVANE</span>
    </div>
    <p class="back-url">www.corvaneretrofitgroup.example</p>
  </section>
</body>
</html>
```